Business Card for Fashion House

We need a business card design for our personalize fashion service for our customers. the business card should reflect reliability, luxury and creativity.
The brand Gravetto is extracted from "Graceful Velvetto"; Gravetto provides fashion designs sprinkled with luxury and style tailored for our elite clients character profile.
Gravetto is created for those who embody class and elegance with a passion for style.
Target Market(s)
Affluent Customers
Industry/Entity Type
Fashion
Contact Information for Business Card
Samira Haddadin
Fashion Designer
Telephone: +971 4 555 0192
Mobile +971 50 555 0147
Emal info@gravetto-example.com
Website www.gravetto-example.com
Social Media Youtube g+ Facebook Instagram Pin /gravetto
Font styles to use
Other font styles liked:
- Audrey provided
Look and feel
Each slider illustrates characteristics of the customer's brand and the style your logo design should communicate.

```html
<!DOCTYPE html>
<html lang="en">
<head>
<meta charset="utf-8">
<title>Gravetto Business Card</title>
<link rel="stylesheet" href="https://fonts.googleapis.com/css2?family=Marcellus&family=Montserrat:wght@400;500&display=swap">
<style>
  :root {
    --page: #1b1b1b;
    --card: #232323;
    --card-edge: #2c2c2c;
    --ink: #ffffff;
    --ink-soft: #e6e6e6;
  }
  * { margin: 0; padding: 0; box-sizing: border-box; }
  html, body { width: 1200px; height: 900px; overflow: hidden; }
  body {
    background: var(--page);
    font-family: "Montserrat", sans-serif;
    color: var(--ink);
    display: flex;
    flex-direction: column;
    align-items: center;
    justify-content: center;
    gap: 40px;
  }
  .card {
    width: 665px;
    height: 380px;
    background: linear-gradient(135deg, var(--card) 0%, var(--card-edge) 100%);
    position: relative;
    box-shadow: 0 10px 30px rgba(0,0,0,.5);
  }
  .brand-mark {
    width: 64px; height: 64px;
    border: 4px solid var(--ink);
    border-radius: 50%;
  }
  .brand-name {
    font-family: "Marcellus", serif;
    font-size: 34px;
    letter-spacing: 0.42em;
    color: var(--ink);
    text-transform: uppercase;
  }
  /* Front */
  .card-front {
    display: flex; flex-direction: column; align-items: center; justify-content: center;
  }
  .card-front .brand-mark { margin-bottom: 26px; }
  .card-front .brand-name { margin-left: 0.42em; }
  .social-handle {
    margin-top: 26px;
    font-size: 18px; font-weight: 500; letter-spacing: 0.08em;
  }
  /* Back */
  .card-back { display: flex; align-items: center; }
  .back-brand {
    width: 340px;
    display: flex; flex-direction: column; align-items: center;
  }
  .back-brand .brand-mark { margin-bottom: 24px; }
  .back-brand .brand-name { font-size: 30px; margin-left: 0.42em; }
  .divider { width: 2px; height: 190px; background: var(--ink); }
  .contact { padding-left: 34px; }
  .person-name {
    font-family: "Marcellus", serif;
    font-size: 22px; letter-spacing: 0.06em; text-transform: uppercase;
  }
  .person-role { font-size: 15px; letter-spacing: 0.06em; color: var(--ink-soft); margin-bottom: 22px; }
  .contact-list { list-style: none; }
  .contact-list li {
    display: flex; align-items: center; gap: 14px;
    font-size: 15px; line-height: 27px; color: var(--ink-soft);
  }
  .contact-list svg { width: 14px; height: 14px; fill: none; stroke: var(--ink); stroke-width: 1.6; flex: none; }
</style>
</head>
<body>
  <section class="card card-front">
    <div class="brand-mark"></div>
    <div class="brand-name">Gravetto</div>
    <div class="social-handle">/gravetto</div>
  </section>

  <section class="card card-back">
    <div class="back-brand">
      <div class="brand-mark"></div>
      <div class="brand-name">Gravetto</div>
    </div>
    <div class="divider"></div>
    <div class="contact">
      <div class="person-name">Samira Haddadin</div>
      <div class="person-role">Fashion Designer</div>
      <ul class="contact-list">
        <li><svg viewBox="0 0 14 14"><path d="M3 1.5l2 2.5-1.2 1.5c.8 1.8 2 3 3.8 3.8L9 8l2.5 2-1 2C6 11.5 2.5 8 2 3.5z"/></svg>+971 4 555 0192</li>
        <li><svg viewBox="0 0 14 14"><rect x="3.5" y="1" width="7" height="12" rx="1"/><path d="M6 11h2"/></svg>+971 50 555 0147</li>
        <li><svg viewBox="0 0 14 14"><rect x="1" y="3" width="12" height="8"/><path d="M1 3l6 5 6-5"/></svg>info@gravetto-example.com</li>
        <li><svg viewBox="0 0 14 14"><circle cx="7" cy="7" r="6"/><ellipse cx="7" cy="7" rx="2.5" ry="6"/><path d="M1 7h12"/></svg>www.gravetto-example.com</li>
      </ul>
    </div>
  </section>
</body>
</html>
```